Mobile Fitness snd Therapy Business Card Design

I need a business card designed for my mobile fitness and therapy business.

Please view the images that I have uploaded. I like the simplicity of the design that I have attached. I adapted it with my information

Target Market(s)

Those seeking personal training, injury rehabilitation or massage therapy.

Industry/Entity Type

Business

Contact Information for Business Card

Derek Fulham - MSc, CAT(C), RMT, CSCS, Pn2
e-mail: derek@vantrelo.com
website: www.vantrelo.com
instagram: @derek_fulham

Font styles to use
Sans Serif

Colors
3176b5
0355a3

Requirements
Must have
• "Contact us to receive a FREE assessment"
• Services offered:
• Personal Training
• Golf Fitness
• Injury Rehab
• Massage Therapy
• Yoga
Nice to have
• Consistent colours with brand
• - Dark Blue: #232837
• - Blue: #5096f0
• Consistent look/feel with the website: www.vantrelo.com

```html
<!DOCTYPE html>
<html lang="en">
<head>
<meta charset="utf-8">
<title>Vantrelo Business Card</title>
<link href="https://fonts.googleapis.com/css2?family=Roboto:wght@400;500;700;900&family=Roboto+Condensed:wght@500;700&display=swap" rel="stylesheet">
<style>
  :root {
    --page-bg: #e4e4e4;
    --card-light: #f4f4f4;
    --navy: #232837;
    --brand-blue: #2a5bd7;
    --text-grey: #3d3f45;
    --white: #ffffff;
  }
  * { margin: 0; padding: 0; box-sizing: border-box; }
  html, body {
    width: 1200px; height: 960px; overflow: hidden;
    background: var(--page-bg);
    font-family: "Roboto", Arial, sans-serif;
  }
  .card {
    position: absolute;
    width: 600px; height: 343px;
    overflow: hidden;
  }
  .card--front { left: 314px; top: 113px; background: var(--card-light); }
  .card--back { left: 311px; top: 472px; background: var(--navy); }

  .brand { position: absolute; left: 0; right: 0; text-align: center; }
  .brand__name {
    font-weight: 900; font-size: 44px; letter-spacing: 6px; line-height: 1;
  }
  .brand__tagline {
    font-weight: 700; font-size: 15.5px; letter-spacing: 2.6px; margin-top: 10px;
  }
  .card--front .brand { top: 58px; color: var(--navy); }
  .card--back .brand { top: 139px; color: var(--white); }
  .card--back .brand__name { font-size: 46px; }
  .card--back .brand__tagline { font-size: 17px; letter-spacing: 3px; margin-top: 14px; }

  .person { position: absolute; top: 155px; left: 0; right: 0; text-align: center; }
  .person__name {
    font-family: "Roboto Condensed", Arial, sans-serif;
    font-weight: 700; font-size: 23px; color: var(--brand-blue); line-height: 1;
  }
  .person__credentials {
    font-family: "Roboto Condensed", Arial, sans-serif;
    font-weight: 700; font-size: 10px; color: var(--brand-blue); margin-top: 4px;
  }
  .contact { position: absolute; top: 203px; left: 0; right: 0; text-align: center;
    font-size: 14px; color: var(--text-grey); line-height: 19px; }
  .contact__item { display: inline-flex; align-items: center; gap: 4px; margin: 0 2px; }
  .contact__item svg { width: 13px; height: 13px; }

  .footer-band {
    position: absolute; left: 0; right: 0; top: 282px; bottom: 0; background: var(--navy);
  }
  .cta {
    position: absolute; top: 265px; left: 59px; width: 483px; height: 34px;
    background: var(--brand-blue); border-radius: 17px;
    color: var(--white); text-align: center; line-height: 34px;
    font-family: "Roboto Condensed", Arial, sans-serif; font-weight: 700; font-size: 21px;
  }
  .services {
    position: absolute; top: 309px; left: 0; right: 0; text-align: center;
    color: var(--white); font-size: 14.5px;
  }
  .services__sep { color: var(--brand-blue); margin: 0 3px; }
</style>
</head>
<body>
  <section class="card card--front">
    <div class="brand">
      <div class="brand__name">VANTRELO</div>
      <div class="brand__tagline">NUTRITION - FITNESS - HEALTH</div>
    </div>

    <div class="person">
      <div class="person__name">DEREK FULHAM</div>
      <div class="person__credentials">MSC, CAT(C), RMT, CSCS, PN2</div>
    </div>

    <div class="contact">
      <div>
        <span class="contact__item">
          <svg viewBox="0 0 14 14" aria-hidden="true"><rect x="1" y="3" width="12" height="8.5" rx="1" fill="#2a5bd7"/><path d="M1.5 3.5 7 8l5.5-4.5" fill="none" stroke="#fff" stroke-width="1.2"/></svg>derek@vantrelo.com
        </span>
        <span class="contact__item">
          <svg viewBox="0 0 14 14" aria-hidden="true"><circle cx="7" cy="7" r="6" fill="#2a5bd7"/><path d="M1 7h12M7 1c-2.5 3-2.5 9 0 12M7 1c2.5 3 2.5 9 0 12" fill="none" stroke="#fff" stroke-width="0.9"/></svg>www.vantrelo.com
        </span>
      </div>
      <div>
        <span class="contact__item">
          <svg viewBox="0 0 14 14" aria-hidden="true"><circle cx="7" cy="7" r="6.5" fill="#2a5bd7"/></svg>@derek_fulham
        </span>
      </div>
    </div>

    <div class="footer-band"></div>
    <div class="cta">CONTACT US TO RECEIVE A FREE ASSESSMENT</div>
    <div class="services">
      Personal Training<span class="services__sep">|</span>Golf Fitness<span class="services__sep">|</span>Injury Rehab<span class="services__sep">|</span>Massage Therapy<span class="services__sep">|</span>Yoga
    </div>
  </section>

  <section class="card card--back">
    <div class="brand">
      <div class="brand__name">VANTRELO</div>
      <div class="brand__tagline">NUTRITION - FITNESS - HEALTH</div>
    </div>
  </section>
</body>
</html>
```